New Business card design to reflect rebrand

I would like a business card design with a good base colour for our new logo and also a placeholder for a profile pic of the card holder. the design needs to be editable to the point that we can easily change the picture of the person and use that design for printmerlo etc. we are looking at a metalic finish business card so will need a good base colour to bring out the finish.

Target Market(s)

prospective customers

Industry/Entity Type

Business

Contact Information for Business Card

I would like one editable design that we can change the name of the card holder and profile picture. The design need to be in a format that be send to printmerlo etc.

Our address is Fenwick Lodge, Copse Lane, Ashcombe Vale, GU14 3TP Tel no. 01483 556172

Requirements
Must have
• place holder for a profile pic for the card holder. in AI or preferably PSD format

```html
<!DOCTYPE html>
<html lang="en">
<head>
<meta charset="utf-8">
<title>Brantley Workplace Services – Business Card</title>
<link rel="stylesheet" href="https://fonts.googleapis.com/css2?family=Open+Sans:wght@400;600;700&display=swap">
<style>
  :root {
    --page: #e9e6e1;
    --card-dark: #1b1c1f;
    --card-mid: #2a2b2f;
    --orange: #f07a1a;
    --orange-deep: #b35610;
    --slate: #4a6583;
    --slate-band: #3f5772;
    --text-light: #e6e6e6;
    --placeholder: #8c8c8c;
  }
  * { box-sizing: border-box; margin: 0; padding: 0; }
  html, body {
    width: 1200px; height: 843px; overflow: hidden;
    background: var(--page);
    font-family: "Open Sans", sans-serif;
  }
  .sheet {
    position: relative; width: 1200px; height: 843px;
    display: flex; flex-direction: column; align-items: center;
    justify-content: center; gap: 22px;
  }
  .card {
    position: relative; width: 680px; height: 389px; overflow: hidden;
    background:
      repeating-linear-gradient(90deg, rgba(255,255,255,0.025) 0 1px, transparent 1px 3px),
      linear-gradient(160deg, var(--card-mid) 0%, var(--card-dark) 55%, #141517 100%);
    box-shadow: 0 6px 18px rgba(0,0,0,0.25);
  }

  /* Back */
  .card-back .brand {
    position: absolute; left: 0; right: 0; top: 140px; text-align: center;
    color: var(--slate); font-weight: 700; font-size: 50px; letter-spacing: 3px;
  }
  .card-back .web {
    position: absolute; left: 0; right: 0; top: 214px; text-align: center;
    color: var(--text-light); font-size: 15px; letter-spacing: 6px;
  }

  /* Front */
  .card-front .logo {
    position: absolute; left: 70px; top: 42px;
    color: var(--orange); font-weight: 700; line-height: 1.05;
  }
  .card-front .logo .name { font-size: 38px; letter-spacing: 2px; display: block; }
  .card-front .logo .sub { font-size: 15px; letter-spacing: 3.2px; display: block; }
  .address {
    position: absolute; left: 70px; top: 158px;
    color: var(--text-light); font-size: 15px; line-height: 21px;
    font-style: normal;
  }
  .phone {
    position: absolute; left: 70px; top: 236px;
    color: var(--text-light); font-size: 15px;
    display: flex; align-items: center; gap: 8px;
  }
  .portrait {
    position: absolute; left: 420px; top: 110px; width: 210px; height: 232px;
    background: linear-gradient(180deg, #9a9a9a 0%, var(--placeholder) 100%);
    border-radius: 90px 90px 0 0;
  }
  .trim { position: absolute; left: 0; bottom: 0; width: 680px; height: 80px; }
  .holder {
    position: absolute; right: 26px; bottom: 16px;
    font-size: 22px; font-weight: 600; color: #ffffff; white-space: nowrap;
  }
  .holder .role { color: var(--orange); font-weight: 400; font-size: 19px; }
</style>
</head>
<body>
<main class="sheet">

  <section class="card card-back" aria-label="Card back">
    <div class="brand">BRANTLEY</div>
    <div class="web">WWW.BRANTLEYWS.COM</div>
  </section>

  <section class="card card-front" aria-label="Card front">
    <div class="logo">
      <span class="name">BRANTLEY</span>
      <span class="sub">WORKPLACE SERVICES</span>
    </div>

    <address class="address">
      Fenwick Lodge<br>
      Copse Lane, Ashcombe Vale<br>
      GU14 3TP
    </address>

    <div class="phone">
      <svg width="12" height="14" viewBox="0 0 12 14" aria-hidden="true">
        <path d="M3 0 L5 3 L3.6 4.6 C4.4 6.8 5.6 8.4 7.4 9.6 L9 8.2 L12 10.4 L10.4 13.4 C5 13 1 8 0.4 1.8 Z" fill="var(--orange)"/>
      </svg>
      <span>01483 556172</span>
    </div>

    <div class="portrait" role="img" aria-label="Profile photo of the card holder"></div>

    <svg class="trim" viewBox="0 0 680 80" aria-hidden="true">
      <polygon points="0,10 300,10 310,16 0,16" fill="var(--orange)"/>
      <polygon points="0,16 310,16 316,20 0,20" fill="var(--orange-deep)"/>
      <polygon points="300,10 680,10 680,80 390,80" fill="var(--slate-band)"/>
    </svg>

    <div class="holder">Tom Ashby - <span class="role">CEO/Founder</span></div>
  </section>

</main>
</body>
</html>
```